uk based ecommerce website requires fresh look ,high quality look and feel

we are a web based company selling eco friendly ground reinforcement grids to diy and construction sectors
our existing website is www.pondermeshpaths.co.uk ,

we have already updated the logo so that is the branding sorted .so we need a ecommerce website that is very much up-to date in design and layout and which has content management system for ease of use so that we can add products and information as required.

Use current logo as reference for colour scheme.
www.pondermeshpaths.co.uk

The current website has 6 pages accessible through the navigation bar, I would now like 5 pages, removing the need for the Trade Enquiries page possibly have it with along with contact us.

Target Market(s)

construction industry , diy end users,
retail market, landscapers, gardeners

Industry/Entity Type

Construction

Font styles to use
Other font styles liked:
• logo font prometo

Colors
f78f20
9bcb3c

Requirements
Must have
• logo colours and logo design in website with cms responsive design for tablet and mobile devices
• expect content to work flawlessly and look great across all devices
• HTML 5 custom design with coding as required
• must have good experiance in ecommerce website design
• eye catching, high quality look and feel and very user friedly ,very up-to date.
Nice to have
• picture slider show
• explain in writing what exactly i am getting in my ecommerce website
Should not have
• plain , basic design , old fashion looking ,cheap look

```html
<!DOCTYPE html>
<html lang="en">
<head>
<meta charset="utf-8">
<title>Pondermesh Ground Solutions</title>
<link rel="stylesheet" href="https://fonts.googleapis.com/css2?family=Open+Sans:wght@300;400;600;700&display=swap">
<style>
:root{
  --orange:#f78f20;
  --green:#9bcb3c;
  --green-dark:#7fae27;
  --ink:#333;
  --muted:#777;
  --line:#e2e2e2;
  --dark:#2b2b2b;
  --darker:#1e1e1e;
  --white:#fff;
}
*{box-sizing:border-box;margin:0;padding:0}
html,body{width:1200px;height:2412px;overflow:hidden}
body{font-family:"Open Sans",Arial,sans-serif;color:var(--ink);background:var(--white);position:relative}
.wrap{width:1024px;margin:0 auto;position:relative}

/* header */
.site-header{height:128px}
.header-top{height:96px}
.brand{position:absolute;left:0;top:20px;display:flex;align-items:center;gap:12px}
.brand-mark{width:52px;height:52px;background:var(--green);border-radius:50%}
.brand-name{font-size:26px;font-weight:700;color:var(--green-dark);line-height:1;text-transform:uppercase;letter-spacing:.5px}
.brand-name small{display:block;font-size:13px;letter-spacing:2px;margin-top:4px}
.top-links{position:absolute;right:200px;top:20px;display:flex;gap:22px;font-size:11px;color:var(--muted)}
.top-links span{display:flex;align-items:center;gap:5px}
.top-links svg{width:12px;height:12px}
.social{position:absolute;right:0;top:14px;display:flex;gap:8px}
.social i{width:24px;height:24px;border-radius:50%;background:var(--orange);display:block}
.search{position:absolute;left:640px;top:56px;width:260px;height:30px;border:1px solid var(--line);display:flex;justify-content:flex-end;align-items:center;padding-right:8px}
.search svg{width:14px;height:14px}
.cart{position:absolute;right:0;top:56px;display:flex;align-items:center;gap:8px;font-size:12px;color:var(--muted)}
.cart b{width:30px;height:30px;background:var(--green);display:flex;align-items:center;justify-content:center}
.cart svg{width:16px;height:16px}

.main-nav{height:32px;background:var(--orange);display:flex}
.main-nav a{color:var(--white);font-size:12px;font-weight:600;text-transform:uppercase;text-decoration:none;flex:1;text-align:center;line-height:32px}
.main-nav a.active{background:var(--green);flex:0 0 110px}

/* hero */
.hero{height:328px;background:linear-gradient(100deg,#8a8f7e 0%,#6d7a55 35%,#4f6a2c 70%,#3c5420 100%);position:relative}
.hero-title{position:absolute;right:110px;top:90px;width:430px;color:var(--white);font-size:27px;font-weight:600;line-height:1.35;text-align:right}
.thumb-strip{height:100px;background:var(--dark);display:flex;justify-content:center;align-items:center;gap:14px}
.thumb-strip span{width:108px;height:66px;background:linear-gradient(#7e8b66,#55663a);display:block}
.thumb-strip span.current{outline:3px solid var(--orange)}

/* sections */
.section-title{text-align:center;font-size:38px;font-weight:300;color:var(--ink)}
.section-title::after{content:"";display:block;width:200px;height:1px;background:var(--line);margin:14px auto 0}
.categories{padding-top:66px}
.cat-grid{margin-top:40px;display:grid;grid-template-columns:repeat(4,238px);column-gap:24px;row-gap:22px}
.cat-card .pic{height:210px;display:block}
.cat-card .pic.selected{outline:4px solid var(--orange);outline-offset:-4px}
.cat-card p{font-size:11px;font-weight:600;text-transform:uppercase;text-align:center;color:var(--ink);line-height:30px}
.pager{display:flex;justify-content:center;gap:8px;margin-top:26px}
.pager b{width:24px;height:24px;background:var(--green);display:flex;align-items:center;justify-content:center}
.pager svg{width:10px;height:10px}

.promo-band{margin-top:56px;height:300px;background:var(--green);display:flex;justify-content:center;align-items:center;gap:34px}
.promo{width:496px;height:232px;position:relative}
.promo.product{background:#8cbb31;border:2px solid rgba(255,255,255,.5)}
.promo.sheet{background:linear-gradient(120deg,#3a3a3a,#1d1d1d)}
.promo h3{position:absolute;color:var(--white);font-size:24px;font-weight:700;line-height:1.15}
.promo p{position:absolute;color:var(--white);font-size:11px;line-height:1.5}
.promo .btn{position:absolute;background:var(--orange);color:var(--white);font-size:11px;font-weight:700;padding:6px 12px;text-transform:uppercase}
.promo .shot{position:absolute;display:block}

.featured{padding-top:100px}
.prod-grid{margin-top:44px;display:grid;grid-template-columns:repeat(4,238px);column-gap:24px}
.prod-card{border:1px solid var(--line);height:284px;position:relative}
.prod-card .pic{height:178px;display:block}
.prod-card h4{font-size:11px;font-weight:700;text-transform:uppercase;text-align:center;margin-top:14px}
.prod-card p{font-size:10px;color:var(--muted);text-align:center;margin-top:4px}
.prod-card .buy{position:absolute;left:14px;right:14px;bottom:14px;display:flex;justify-content:space-between;align-items:center;border-top:1px solid var(--line);padding-top:10px}
.prod-card .price{font-size:13px;font-weight:600}
.prod-card .add{background:var(--orange);color:var(--white);font-size:10px;font-weight:700;padding:5px 12px}
.featured .pager{margin-top:64px}

/* footer */
.site-footer{position:absolute;left:0;top:2262px;width:1200px;height:130px;background:var(--dark);color:#bbb}
.site-footer .wrap{display:flex;padding-top:14px}
.foot-col{width:200px;font-size:10px;line-height:15px}
.foot-col h5{color:var(--white);font-size:13px;font-weight:600;margin-bottom:6px}
.foot-col.contact{width:260px}
.foot-col.contact span{display:flex;gap:6px;align-items:center}
.foot-col svg{width:10px;height:10px}
.foot-brand{margin-left:auto;display:flex;align-items:center;gap:10px;margin-top:18px}
.foot-brand i{width:40px;height:40px;border-radius:50%;background:#666;display:block}
.foot-brand span{color:#888;font-size:20px;font-weight:700;text-transform:uppercase;line-height:1}
.foot-brand small{display:block;font-size:10px;letter-spacing:2px;margin-top:3px}
.bottom-bar{position:absolute;left:0;top:2392px;width:1200px;height:20px;background:var(--darker);font-size:9px;color:#999}
.bottom-bar .wrap{display:flex;justify-content:space-between;align-items:center;height:20px}
.cards{display:flex;gap:4px}
.cards i{width:22px;height:12px;background:#555;display:block}
</style>
</head>
<body>
<header class="site-header">
  <div class="wrap header-top">
    <div class="brand"><span class="brand-mark"></span><span class="brand-name">Pondermesh<small>Ground Solutions</small></span></div>
    <div class="top-links">
      <span><svg viewBox="0 0 12 12"><circle cx="6" cy="6" r="5" fill="none" stroke="#999"/></svg>www.pondermeshpaths.co.uk</span>
      <span><svg viewBox="0 0 12 12"><path d="M3 1l2 3-1 1c1 2 2 3 3 3l1-1 3 2-1 2C5 11 1 7 1 3z" fill="#999"/></svg>0161 555 0142</span>
      <span>My Account</span>
      <span>Login</span>
    </div>
    <div class="social"><i></i><i></i><i></i><i></i></div>
    <div class="search"><svg viewBox="0 0 14 14"><circle cx="6" cy="6" r="4.5" fill="none" stroke="#999" stroke-width="1.5"/><path d="M9 9l4 4" stroke="#999" stroke-width="1.5"/></svg></div>
    <div class="cart"><b><svg viewBox="0 0 16 16"><path d="M1 2h3l2 8h7l2-6H5" fill="none" stroke="#fff" stroke-width="1.5"/><circle cx="7" cy="13" r="1.3" fill="#fff"/><circle cx="12" cy="13" r="1.3" fill="#fff"/></svg></b>0 item(s)</div>
  </div>
  <nav class="main-nav wrap">
    <a class="active" href="#">Home</a><a href="#">Shop</a><a href="#">About Us</a><a href="#">Ground Solutions</a><a href="#">Pondermesh</a><a href="#">Contact Us</a>
  </nav>
</header>

<section class="hero" role="img" aria-label="Garden path laid with gravel stabilisation grid beside a lawn">
  <h1 class="hero-title">We Specialize in Stabilisation Grid Systems For Gravel &amp; Grass Surfaces</h1>
</section>
<div class="thumb-strip">
  <span role="img" aria-label="Gravel driveway"></span><span role="img" aria-label="Grid panels"></span><span class="current" role="img" aria-label="Garden path"></span><span role="img" aria-label="House driveway"></span><span role="img" aria-label="Grass parking"></span><span role="img" aria-label="Laying grid"></span>
</div>

<section class="categories wrap">
  <h2 class="section-title">Select Product Category</h2>
  <div class="cat-grid">
    <div class="cat-card"><span class="pic selected" role="img" aria-label="Geotextile membrane roll" style="background:linear-gradient(#d9d6cc,#a9a49a)"></span><p>Geotextile Membranes</p></div>
    <div class="cat-card"><span class="pic" role="img" aria-label="Light domestic gravel driveway" style="background:linear-gradient(#bdb7a6,#857d6a)"></span><p>Light Domestic Driveways</p></div>
    <div class="cat-card"><span class="pic" role="img" aria-label="Heavy domestic driveway grid" style="background:linear-gradient(#6e6e6e,#2e2e2e)"></span><p>Heavy Domestic Driveways</p></div>
    <div class="cat-card"><span class="pic" role="img" aria-label="Commercial parking grid" style="background:linear-gradient(#9a9a9a,#5a5a5a)"></span><p>Commercial Parking System</p></div>
    <div class="cat-card"><span class="pic" role="img" aria-label="Paving and pathway grid" style="background:linear-gradient(#a0a89a,#5d6a52)"></span><p>Parking &amp; Pathway Systems</p></div>
    <div class="cat-card"><span class="pic" role="img" aria-label="Equestrian ground grid" style="background:linear-gradient(#8d9e6f,#3e4d2e)"></span><p>Equestrian Grid</p></div>
    <div class="cat-card"><span class="pic" role="img" aria-label="Steel ground pins" style="background:linear-gradient(#4b4b4b,#1d1d1d)"></span><p>Steel U Pins</p></div>
    <div class="cat-card"><span class="pic" role="img" aria-label="Garden lawn edging" style="background:linear-gradient(#a6c36a,#58752b)"></span><p>Garden Edging</p></div>
  </div>
  <div class="pager"><b><svg viewBox="0 0 10 10"><path d="M7 1L3 5l4 4" fill="none" stroke="#fff" stroke-width="2"/></svg></b><b><svg viewBox="0 0 10 10"><path d="M3 1l4 4-4 4" fill="none" stroke="#fff" stroke-width="2"/></svg></b></div>
</section>

<section class="promo-band">
  <div class="promo product">
    <h3 style="left:24px;top:26px">PONDERMESH 25<br><span style="font-size:14px;font-weight:600">The Stabilising Grid</span></h3>
    <p style="left:24px;top:100px;width:200px">Lorem ipsum dolor sit amet consectetur adipiscing elit sed do eiusmod tempor incididunt ut labore.</p>
    <span class="btn" style="left:24px;top:176px">Download PDF</span>
    <span class="shot" role="img" aria-label="Stack of black grid panels" style="left:262px;top:40px;width:210px;height:168px;background:linear-gradient(135deg,#3c3c3c,#151515)"></span>
  </div>
  <div class="promo sheet">
    <span class="shot" role="img" aria-label="Honeycomb gravel grid close-up" style="left:0;top:0;width:300px;height:228px;background:linear-gradient(135deg,#4a4a4a,#222)"></span>
    <h3 style="right:24px;top:26px;text-align:right">Gravel<br>Grid<br><span style="font-size:18px">Data Sheet</span></h3>
    <p style="right:24px;top:130px;width:150px;text-align:right">Lorem ipsum dolor sit amet consectetur adipiscing.</p>
    <span class="btn" style="right:24px;top:188px">Download PDF</span>
  </div>
</section>

<section class="featured wrap">
  <h2 class="section-title">Feature Products</h2>
  <div class="prod-grid">
    <div class="prod-card"><span class="pic" role="img" aria-label="Gravel filled grid" style="background:linear-gradient(#b9b4a6,#8b8577)"></span><h4>Pondermesh 25 System</h4><p>Lorem Ipsum Dolor Sit Amet Consec</p><div class="buy"><span class="price">£ 11.00</span><span class="add">Add</span></div></div>
    <div class="prod-card"><span class="pic" role="img" aria-label="Grid laid on a building site" style="background:linear-gradient(#a5a29a,#6b675d)"></span><h4>Terralock 40 Paving System</h4><p>Lorem Ipsum Dolor Sit Amet Consec</p><div class="buy"><span class="price">£ 9.30</span><span class="add">Add</span></div></div>
    <div class="prod-card"><span class="pic" role="img" aria-label="House with gravel driveway" style="background:linear-gradient(#9fb3c8,#7b7262)"></span><h4>Pondermesh 25 System</h4><p>Lorem Ipsum Dolor Sit Amet Consec</p><div class="buy"><span class="price">£ 11.00</span><span class="add">Add</span></div></div>
    <div class="prod-card"><span class="pic" role="img" aria-label="Black grid on lawn" style="background:linear-gradient(#6d8a3c,#2a2a2a)"></span><h4>Terralock 40 Paving System</h4><p>Lorem Ipsum Dolor Sit Amet Consec</p><div class="buy"><span class="price">£ 9.30</span><span class="add">Add</span></div></div>
  </div>
  <div class="pager"><b><svg viewBox="0 0 10 10"><path d="M7 1L3 5l4 4" fill="none" stroke="#fff" stroke-width="2"/></svg></b><b><svg viewBox="0 0 10 10"><path d="M3 1l4 4-4 4" fill="none" stroke="#fff" stroke-width="2"/></svg></b></div>
</section>

<footer class="site-footer">
  <div class="wrap">
    <div class="foot-col"><h5>Quick Link</h5>Home<br>Shop<br>About Us<br>Ground Solutions<br>Pondermesh<br>Contact Us</div>
    <div class="foot-col"><h5>My Account</h5>My Account<br>Order History<br>Wish List<br>Cart</div>
    <div class="foot-col contact"><h5>Contact Details</h5>
      <span><svg viewBox="0 0 10 10"><path d="M5 0a3 3 0 0 1 3 3c0 3-3 7-3 7S2 6 2 3a3 3 0 0 1 3-3z" fill="#bbb"/></svg>Unit 4 Meadow Works, Bank Lane,</span>
      <span style="padding-left:16px">Oakfield, Lancashire, LA9 4QT</span>
      <span><svg viewBox="0 0 10 10"><path d="M2 0l2 3-1 1c1 2 2 3 3 3l1-1 3 2-1 2C4 10 0 6 0 2z" fill="#bbb"/></svg>0161 555 0142</span>
      <span><svg viewBox="0 0 10 10"><path d="M2 0l2 3-1 1c1 2 2 3 3 3l1-1 3 2-1 2C4 10 0 6 0 2z" fill="#bbb"/></svg>0161 555 0143</span>
      <span><svg viewBox="0 0 10 10"><rect x="0" y="2" width="10" height="6" fill="none" stroke="#bbb"/><path d="M0 2l5 3 5-3" fill="none" stroke="#bbb"/></svg>info@pondermeshpaths.co.uk</span>
    </div>
    <div class="foot-brand"><i></i><span>Pondermesh<small>Ground Solutions</small></span></div>
  </div>
</footer>
<div class="bottom-bar"><div class="wrap"><span>Copyright © 2016 Pondermesh Ground Solutions. All Rights Reserved. | Terms of Service | Site Map</span><span class="cards"><i></i><i></i><i></i><i></i><i></i></span></div></div>
</body>
</html>
```